Digital & Print Graphic Design templates for Comedy Club

We need new new digital & print graphic design templates for our upcoming comedy events created for use in CANVA in the following specs
Digital:
1080x1080px
1200x600px
800x400px
1920x1080px
1080x1355px
1500x500px
851x315px
Print
11x17"
22x28"
95.5x30"

Target Market(s)

18+ comedy fans

Industry/Entity Type

comedy club

Font styles to use
Sans Serif

Colors
FFF300
FFF600
FEFA6F
FFFEC7
FFFEE8
6B429C
8869AF
B7A5CE
E3DAEB
F3F0F8

Requirements
Must have
• templates must be CANVA compatible. frame for comedian photo.
Nice to have
• would like to incorporate deep purple into the design
Should not have
• do not include phone number on any templates

```html
<!DOCTYPE html>
<html lang="en">
<head>
<meta charset="utf-8">
<title>The Grin Room – Event Templates</title>
<link href="https://fonts.googleapis.com/css2?family=Archivo+Black&family=Montserrat:wght@600;700;800;900&display=swap" rel="stylesheet">
<style>
  :root{
    --yellow:#FFF300;
    --yellow-soft:#FEFA6F;
    --purple:#6B429C;
    --purple-mid:#8869AF;
    --lavender:#B7A5CE;
    --lavender-pale:#E3DAEB;
    --purple-deep:#3b1b6b;
    --purple-dark:#2a1150;
    --name:#7a3cc8;
    --ink:#111;
    --white:#fff;
    --label:#a6a6a6;
  }
  *{box-sizing:border-box;margin:0;padding:0}
  html,body{width:1200px;height:990px;overflow:hidden;background:var(--white)}
  .sheet{position:relative;width:1200px;height:990px;font-family:'Montserrat',sans-serif}

  .size-label{position:absolute;font-family:'Montserrat',sans-serif;font-weight:800;font-size:21px;color:var(--label);transform:translateX(-50%);letter-spacing:.5px}

  .brand-mark{position:absolute;left:50px;top:110px;width:350px;height:350px;border-radius:50%;background:var(--ink);border:8px solid var(--yellow);display:flex;align-items:center;justify-content:center}
  .brand-mark .brand-name{font-family:'Archivo Black',sans-serif;color:var(--yellow);font-size:54px;line-height:1;text-align:center}

  .panel{position:absolute;overflow:hidden;background:radial-gradient(ellipse at 60% 40%,var(--purple) 0%,var(--purple-deep) 70%,var(--purple-dark) 100%)}

  .name-banner{position:absolute;background:var(--yellow);display:flex;align-items:center;justify-content:center;transform:rotate(-2.5deg)}
  .name-banner .name{font-family:'Archivo Black',sans-serif;color:var(--name);white-space:nowrap;line-height:1;text-shadow:2px 2px 0 #3a1b66}

  .date-box{position:absolute;background:var(--purple-mid);color:var(--white);font-weight:800;line-height:1.1;transform:rotate(-2.5deg);padding:4px 10px;display:flex;flex-direction:column;justify-content:center}

  .outline-text{position:absolute;font-family:'Montserrat',sans-serif;font-weight:900;color:transparent;-webkit-text-stroke:1.3px var(--lavender-pale);line-height:1;transform:rotate(-2.5deg);white-space:nowrap}
  .sub-text{position:absolute;font-weight:800;color:var(--lavender);white-space:nowrap;transform:rotate(-2.5deg)}

  .photo{position:absolute;background:linear-gradient(160deg,#5b4a6e 0%,#2c2233 60%,#1b1420 100%);border-radius:40% 40% 0 0}

  .mascot{position:absolute;background:var(--yellow);border-radius:40% 40% 30% 30%}

  .tape{position:absolute;left:-40px;background:var(--yellow);display:flex;align-items:center;overflow:hidden;white-space:nowrap;font-family:'Archivo Black',sans-serif;color:var(--ink)}

  .badge{position:absolute;border-radius:50%;background:var(--ink);border:3px solid var(--yellow);display:flex;align-items:center;justify-content:center;transform:translate(-50%,-50%)}
  .badge .brand-name{font-family:'Archivo Black',sans-serif;color:var(--yellow);line-height:1;text-align:center}

  .site-url{position:absolute;color:var(--white);font-weight:800;letter-spacing:3px;transform:rotate(-4deg);white-space:nowrap}
</style>
</head>
<body>
<main class="sheet">

  <span class="size-label" style="left:602px;top:25px">800*400PX</span>
  <span class="size-label" style="left:967px;top:25px">1080*1355PX</span>
  <span class="size-label" style="left:594px;top:520px">1920*1080</span>
  <span class="size-label" style="left:227px;top:936px">1080*1080PX</span>
  <span class="size-label" style="left:794px;top:936px">1200*600PX</span>

  <div class="brand-mark"><span class="brand-name">THE<br>GRIN<br>ROOM</span></div>

  <!-- 800 x 400 -->
  <section class="panel" style="left:441px;top:61px;width:323px;height:241px">
    <div class="photo" role="img" aria-label="Comedian photo frame" style="left:225px;top:55px;width:110px;height:190px"></div>
    <div class="name-banner" style="left:-5px;top:18px;width:330px;height:52px"><span class="name" style="font-size:33px">MILO VARGA</span></div>
    <div class="date-box" style="left:12px;top:82px;width:210px;height:48px;font-size:15px"><span>JANUARY 30–31,</span><span>FRIDAY–SATURDAY</span></div>
    <div class="mascot" role="img" aria-label="Microphone mascot" style="left:25px;top:158px;width:24px;height:36px"></div>
    <div class="tape" style="top:190px;width:420px;height:20px;font-size:9px;transform:rotate(-4deg)">THE GRIN ROOM &nbsp;|&nbsp; THE GRIN ROOM &nbsp;|&nbsp; THE GRIN ROOM &nbsp;|&nbsp; THE GRIN ROOM &nbsp;|&nbsp; THE GRIN ROOM</div>
    <div class="badge" style="left:134px;top:183px;width:82px;height:82px"><span class="brand-name" style="font-size:15px">THE<br>GRIN<br>ROOM</span></div>
  </section>

  <!-- 1080 x 1355 -->
  <section class="panel" style="left:780px;top:61px;width:359px;height:449px">
    <div class="photo" role="img" aria-label="Comedian photo frame" style="left:170px;top:150px;width:200px;height:310px"></div>
    <div class="name-banner" style="left:15px;top:36px;width:320px;height:52px"><span class="name" style="font-size:40px">REMY OKAFOR</span></div>
    <div class="date-box" style="left:20px;top:94px;width:255px;height:72px"><span style="font-size:20px">FRIDAY – SUNDAY</span><span style="font-size:34px">APRIL 3 – 5</span></div>
    <div class="outline-text" style="left:30px;top:175px;font-size:34px;line-height:1.05">EXCLUSIVE<br>CONCERT<br>EVENT</div>
    <div class="mascot" role="img" aria-label="Microphone mascot" style="left:38px;top:330px;width:44px;height:66px"></div>
    <div class="tape" style="top:385px;width:460px;height:28px;font-size:11px;transform:rotate(-8deg)">THE GRIN ROOM &nbsp;|&nbsp; THE GRIN ROOM &nbsp;|&nbsp; THE GRIN ROOM &nbsp;|&nbsp; THE GRIN ROOM &nbsp;|&nbsp; THE GRIN ROOM</div>
    <div class="badge" style="left:275px;top:385px;width:102px;height:102px"><span class="brand-name" style="font-size:19px">THE<br>GRIN<br>ROOM</span></div>
  </section>

  <!-- 1920 x 1080 -->
  <section class="panel" style="left:440px;top:328px;width:324px;height:182px">
    <div class="photo" role="img" aria-label="Comedian photo frame" style="left:218px;top:10px;width:110px;height:175px"></div>
    <div class="name-banner" style="left:10px;top:18px;width:225px;height:32px"><span class="name" style="font-size:22px">OWEN PRATLEY</span></div>
    <div class="date-box" style="left:15px;top:56px;width:200px;height:22px;font-size:10px">APRIL 3–4, FRIDAY–SATURDAY</div>
    <div class="outline-text" style="left:20px;top:92px;font-size:25px">EXCLUSIVE</div>
    <div class="outline-text" style="left:22px;top:120px;font-size:17px">CONCERT EVENT</div>
    <div class="mascot" role="img" aria-label="Microphone mascot" style="left:193px;top:85px;width:14px;height:22px"></div>
    <div class="tape" style="top:155px;width:420px;height:14px;font-size:7px;transform:rotate(-4deg)">THE GRIN ROOM &nbsp;|&nbsp; THE GRIN ROOM &nbsp;|&nbsp; THE GRIN ROOM &nbsp;|&nbsp; THE GRIN ROOM &nbsp;|&nbsp; THE GRIN ROOM &nbsp;|&nbsp; THE GRIN ROOM</div>
    <div class="badge" style="left:210px;top:141px;width:62px;height:62px"><span class="brand-name" style="font-size:11px">THE<br>GRIN<br>ROOM</span></div>
  </section>

  <!-- 1080 x 1080 -->
  <section class="panel" style="left:57px;top:565px;width:356px;height:356px">
    <div class="photo" role="img" aria-label="Comedian photo frame" style="left:85px;top:95px;width:205px;height:270px"></div>
    <div class="name-banner" style="left:18px;top:20px;width:320px;height:50px"><span class="name" style="font-size:38px">DAN HOLLOWAY</span></div>
    <div class="date-box" style="left:20px;top:80px;width:145px;height:60px"><span style="font-size:18px">WEDNESDAY</span><span style="font-size:22px">04.02.2026</span></div>
    <div class="outline-text" style="left:225px;top:92px;font-size:38px">LIVE</div>
    <div class="sub-text" style="left:218px;top:132px;font-size:12px">AT GRIN ROOM</div>
    <div class="mascot" role="img" aria-label="Microphone mascot" style="left:12px;top:285px;width:28px;height:42px"></div>
    <div class="tape" style="top:305px;width:460px;height:18px;font-size:8px;transform:rotate(-7deg)">THE GRIN ROOM &nbsp;|&nbsp; THE GRIN ROOM &nbsp;|&nbsp; THE GRIN ROOM &nbsp;|&nbsp; THE GRIN ROOM &nbsp;|&nbsp; THE GRIN ROOM &nbsp;|&nbsp; THE GRIN ROOM</div>
    <div class="badge" style="left:264px;top:288px;width:80px;height:80px"><span class="brand-name" style="font-size:14px">THE<br>GRIN<br>ROOM</span></div>
  </section>

  <!-- 1200 x 600 -->
  <section class="panel" style="left:438px;top:565px;width:713px;height:356px">
    <div class="photo" role="img" aria-label="Comedian photo frame" style="left:10px;top:20px;width:225px;height:345px"></div>
    <div class="name-banner" style="left:182px;top:48px;width:480px;height:78px"><span class="name" style="font-size:50px">DAN HOLLOWAY</span></div>
    <div class="date-box" style="left:228px;top:140px;width:240px;height:92px"><span style="font-size:30px">WEDNESDAY</span><span style="font-size:38px">04.02.2026</span></div>
    <div class="outline-text" style="left:505px;top:138px;font-size:38px">LIVE AT</div>
    <div class="sub-text" style="left:508px;top:180px;font-size:22px">GRIN ROOM</div>
    <div class="mascot" role="img" aria-label="Microphone mascot" style="left:185px;top:245px;width:26px;height:40px"></div>
    <div class="site-url" style="left:228px;top:245px;font-size:17px">GRINROOMCOMEDY.COM</div>
    <div class="tape" style="top:300px;width:820px;height:24px;font-size:11px;transform:rotate(-3deg)">THE GRIN ROOM &nbsp;|&nbsp; THE GRIN ROOM &nbsp;|&nbsp; THE GRIN ROOM &nbsp;|&nbsp; THE GRIN ROOM &nbsp;|&nbsp; THE GRIN ROOM &nbsp;|&nbsp; THE GRIN ROOM &nbsp;|&nbsp; THE GRIN ROOM &nbsp;|&nbsp; THE GRIN ROOM</div>
    <div class="badge" style="left:623px;top:271px;width:130px;height:130px"><span class="brand-name" style="font-size:23px">THE<br>GRIN<br>ROOM</span></div>
  </section>

</main>
</body>
</html>
```